Flyer Design Project

I need a cool design that describes a new line of services I am selling. The final product should be a 8 1/2 by 11 and maximum two pages.

I am selling consulting services to learn to use web conferencing tools for business development, meeting and training.
Updates

Please use the file I have attached as a guide for your work. It is a document called "guide-quickofficehints" and I love its design.

Thanks

                                        Please substitute the new text availble and just uploaded in the FLYER. Please submit the FINAL version fo your design with TExt changes as well as improvements detailed in previous message. 

Target Market(s)

Entrepreneurs and classroom educators who wnats to explore a new way to teach (innovators not scared of technology)

Industry/Entity Type

Business

Requirements
Must have
• I would like to receive a final PDF with the content EDITABLE for minor edits (I have acrobat)
Logo should be included (attached)

PLEASE CHECK OUT ATTACHED DOCUMENT WHOSE DESIGN I LOVE.
IT is called "Guide quick-office hints". If you could follow that as a template to design mine that would be great!

```html
<!DOCTYPE html>
<html lang="en">
<head>
<meta charset="utf-8">
<title>Online Meeting Skills Services – Flyer</title>
<link rel="stylesheet" href="https://fonts.googleapis.com/css2?family=Arimo:wght@400;700&display=swap">
<style>
  :root {
    --orange: #f07a1e;
    --orange-deep: #e2661a;
    --brown: #7a3b12;
    --ink: #1f1f1f;
    --white: #ffffff;
    --dark-1: #1a0f06;
    --dark-2: #5a3312;
    --dark-3: #a0622a;
    --row-1: #fff6d8;
    --row-2: #feeedc;
    --row-3: #fde6d5;
    --row-4: #fddfd0;
    --stripe-1: #f7c21b;
    --stripe-2: #f5a12a;
    --stripe-3: #f07f22;
    --stripe-4: #ea5524;
  }
  * { box-sizing: border-box; margin: 0; padding: 0; }
  html, body { width: 849px; height: 1200px; overflow: hidden; background: var(--white); }
  body { font-family: "Arimo", Arial, sans-serif; color: var(--ink); }

  .flyer { position: relative; width: 849px; height: 1200px; overflow: hidden; background: var(--white); }

  .backdrop { position: absolute; inset: 0; }

  .brand {
    position: absolute; top: 62px; right: 48px;
    display: flex; align-items: center; gap: 10px;
    font-size: 26px; font-weight: 400; color: var(--ink); letter-spacing: 0.5px;
  }
  .brand__dot { width: 16px; height: 16px; border-radius: 50%; background: var(--orange); }

  .hero-title {
    position: absolute; left: 152px; top: 258px; color: var(--white); font-weight: 700;
    text-shadow: 0 1px 2px rgba(0,0,0,0.35);
  }
  .hero-title__main { font-size: 66px; line-height: 60px; letter-spacing: 1px; }
  .hero-title__sub { font-size: 33px; line-height: 36px; margin-top: 6px; }
  .hero-title__tagline { font-size: 23px; line-height: 28px; margin-top: 2px; }

  .content { position: absolute; left: 234px; top: 510px; width: 574px; }

  .lead-question {
    background: var(--orange); color: var(--white);
    font-size: 20.5px; font-weight: 700; line-height: 29px;
    padding: 11px 20px 11px 20px; border-radius: 0 22px 22px 0;
    height: 81px;
  }

  .body-copy { margin-top: 23px; font-size: 14px; line-height: 20.6px; text-align: justify; }
  .body-copy p + p { margin-top: 9px; }

  .service-list { list-style: none; margin-top: 8px; }
  .service-list li {
    position: relative; padding: 9px 8px 9px 26px;
    font-size: 14px; line-height: 20.6px; text-align: justify;
    border-top: 1px solid #f3b27a;
  }
  .service-list li::before { content: ""; position: absolute; left: 0; top: 0; bottom: 0; width: 14px; border-radius: 6px 0 0 6px; }
  .service-list li:last-child { border-bottom: 1px solid #f3b27a; }
  .service-list .arrow { color: var(--brown); margin-right: 4px; }
  .service-list li:nth-child(1) { background: var(--row-1); }
  .service-list li:nth-child(1)::before { background: var(--stripe-1); }
  .service-list li:nth-child(2) { background: var(--row-2); }
  .service-list li:nth-child(2)::before { background: var(--stripe-2); }
  .service-list li:nth-child(3) { background: var(--row-3); }
  .service-list li:nth-child(3)::before { background: var(--stripe-3); }
  .service-list li:nth-child(4) { background: var(--row-4); }
  .service-list li:nth-child(4)::before { background: var(--stripe-4); }
</style>
</head>
<body>
<main class="flyer">
  <svg class="backdrop" width="849" height="1200" viewBox="0 0 849 1200" aria-hidden="false">
    <defs>
      <radialGradient id="heroGlow" cx="0.72" cy="0.35" r="0.75">
        <stop offset="0" stop-color="var(--dark-3)"/>
        <stop offset="0.45" stop-color="var(--dark-2)"/>
        <stop offset="1" stop-color="var(--dark-1)"/>
      </radialGradient>
    </defs>
    <path class="accent-curve" d="M238 0 Q -50 640 170 1200" fill="none" stroke="var(--orange)" stroke-width="2"/>
    <rect class="hero-band" x="0" y="147" width="849" height="344" fill="var(--orange)"/>
    <path class="hero-image" role="img" aria-label="Dark amber image of streaming computer code and glowing light trails circling a globe of binary digits"
          d="M172 147 Q150 320 150 491 L849 491 L849 147 Z" fill="url(#heroGlow)"/>
  </svg>

  <div class="brand">
    <span class="brand__dot"></span>
    <span class="brand__name">Meetwell consulting</span>
  </div>

  <header class="hero-title">
    <div class="hero-title__main">ONLINE<br>MEETING</div>
    <div class="hero-title__sub">SKILLS SERVICES</div>
    <div class="hero-title__tagline">It is just the beginning...</div>
  </header>

  <section class="content">
    <h2 class="lead-question">What if your business can reach all the people already interested in learning what you know?</h2>

    <div class="body-copy">
      <p>A different use of webinar technology: the first step towards a new way of thinking about your markets/your clients.</p>
      <p>You probably know about webinars. You may have attended a few yourself. Perhaps you found them boring and un-engaging, with no chance to interact or ask questions to a guarded speaker. Did the speaker drone on as you – yes, you! – checked your email? Good news: we are not talking about “that” kind of webinars. Yes: there is another way!</p>
      <p>Turn your expertise into engaging and interactive online sessions delivered “live”! Engage people online in conversations that matter to them and forget about the technical details, the mailing list or selecting the right webinar technology. We can provide a turnkey solution, that in two-week time offers you all you need to break into this new technology from the front-door. In fact:</p>
    </div>

    <ul class="service-list">
      <li><span class="arrow">➥</span>We design an effective virtual meeting experience for you using the tools of the online room to their full potential through a different way of thinking about online participant engagement and interactivity.</li>
      <li><span class="arrow">➥</span>We repurpose your marketing materials for engaging collaborative online meeting and learning.</li>
      <li><span class="arrow">➥</span>We develop and execute a communication plan to market your online sessions to your mailing list - already interested in learning about your expertise – and to others.</li>
      <li><span class="arrow">➥</span>We support you “hands-on” as you deliver a synchronous (live and online) session in your own virtual training room. We orchestrate a rehearsal and you show up on the day of the session ready to engage your remote participants.</li>
    </ul>
  </section>
</main>
</body>
</html>
```